Long webpage to explain and sell a complex concept

Accountancy firm wishes to explain Management Accounting to a Small Business audience. We have written the text, assembled a couple of charts and quotes and some concept photos.
There is a lot of text and it is required to explain this type of accounting.
Rather than have a long single block of text which is less likely to be read, we want to break it up with pictures, appropriate white space, diagrams etc. Someone landing on this page will then scroll down reading the text which is designed to keep you reading more.
The page on the website where this will go is https://www.brindlequay.com.au/services/management-accountants-perth/
So the fonts/colours need to fit in. Notice there is a pallet of colours which can be seen here: https://www.brindlequay.com.au/services/

Target Market(s)

Small Business owners in Perth, Western Australia

Number of Pages Required

1 page

Requirements
Must have
• The look and feel needs to match the website indicated in the description above. However we're happy to make the design of this page more interesting than the rest of the site.

```html
<!DOCTYPE html>
<html lang="en">
<head>
<meta charset="utf-8">
<title>Management Accounting | Brindle Quay</title>
<link href="https://fonts.googleapis.com/css2?family=Arimo:wght@400;700&family=Open+Sans:ital,wght@0,400;0,600;0,700;1,600;1,700&display=swap" rel="stylesheet">
<style>
:root{
  --teal:#1192b3;
  --teal-dark:#0b7f9d;
  --heading:#1a8db0;
  --ink:#3d4a55;
  --body:#555c63;
  --navy:#3e5a70;
  --navy-mid:#37536a;
  --navy-deep:#2d475b;
  --white:#ffffff;
}
*{margin:0;padding:0;box-sizing:border-box}
html,body{width:1200px;height:3948px;overflow:hidden;background:var(--white)}
body{font-family:"Open Sans",sans-serif;color:var(--body);position:relative}
.block{position:absolute;left:0;width:1200px}
h1,h2,h3,.nav,.brand{font-family:"Arimo",sans-serif}

.topbar{top:0;height:43px;background:var(--teal);color:var(--white);font-size:12px;display:flex;align-items:center;padding:0 112px}
.topbar .item{display:flex;align-items:center;gap:8px;margin-right:22px}
.topbar .social{margin-left:auto;display:flex;gap:10px}
.dot{width:10px;height:10px;border-radius:50%;background:var(--white);display:inline-block}

.header{top:43px;height:67px;display:flex;align-items:center;padding:0 112px;border-bottom:1px solid #e4e8eb}
.brand{font-size:27px;font-weight:700;color:var(--navy);letter-spacing:-.5px}
.brand small{display:block;font-family:"Open Sans",sans-serif;font-size:9px;font-weight:600;color:var(--teal);letter-spacing:0;margin:2px 0 0 32px}
.nav{margin-left:auto;display:flex;align-items:center;gap:26px;font-size:14px;font-weight:700;color:var(--ink)}
.nav .active{color:var(--teal);border-bottom:2px solid var(--teal);padding-bottom:4px;margin-top:6px}
.btn{background:var(--teal);color:var(--white);font-family:"Arimo",sans-serif;font-size:14px;padding:10px 14px;border-radius:3px}

.hero{top:110px;height:242px;background:linear-gradient(180deg,#5e6b86 0%,#9aa2b2 35%,#d7dade 55%,#6f7a86 78%,#3d4a57 100%)}
.hero .band{position:absolute;left:0;bottom:0;width:100%;height:69px;background:rgba(20,70,100,.72)}
.hero h1{position:absolute;left:112px;bottom:14px;color:var(--white);font-size:36px;font-weight:700}

.intro{top:404px;padding:0 110px;font-size:14px;line-height:27.5px;text-align:justify;text-align-last:center;color:#666}

.video{top:647px;height:475px;background:var(--teal)}
.video .photo{position:absolute;left:0;top:0}
.video .copy{position:absolute;left:634px;top:62px;width:460px;display:flex;flex-direction:column}
.video h2{color:var(--white);font-size:33px;line-height:40px;font-weight:700;white-space:nowrap;letter-spacing:-.3px}
.video blockquote{margin-top:14px;color:var(--white);font-size:15.5px;line-height:31px;font-style:italic;font-weight:700;text-align:justify}

.feature{height:372px}
.feature h2{color:var(--heading);font-size:33px;line-height:38px;font-weight:700;white-space:nowrap;letter-spacing:-.3px}
.feature p{font-size:13.5px;line-height:25.7px;text-align:justify;margin-top:14px;color:#555}
.feature .text{position:absolute;width:465px}
.feature .img{position:absolute;width:465px;height:370px}

.plband{top:2101px;height:345px;background:linear-gradient(120deg,#0a72b4 0%,#1488c8 50%,#1aa0d8 100%);text-align:center;color:var(--white)}
.plband h2{font-size:35px;font-weight:700;margin-top:58px}
.plband p{font-size:13.5px;line-height:26.5px;margin:16px auto 0;width:936px;text-align:justify;text-align-last:center}

.cta{top:3413px;height:124px;background:var(--teal);color:var(--white)}
.cta p{position:absolute;left:112px;top:36px;font-family:"Arimo",sans-serif;font-size:22px;line-height:28px}
.cta .btn-light{position:absolute;left:904px;top:40px;width:184px;height:40px;background:var(--white);color:var(--teal);border-radius:3px;font-family:"Arimo",sans-serif;font-size:14px;display:flex;align-items:center;justify-content:center}

.footer{top:3537px;height:411px;background:linear-gradient(180deg,var(--navy) 0%,var(--navy-mid) 100%);color:var(--white)}
.footer .brand{position:absolute;left:116px;top:54px;color:var(--white);font-size:28px}
.footer .brand small{color:#cfe3ee}
.footer .contact{position:absolute;top:56px;font-family:"Open Sans",sans-serif;font-size:15px;font-weight:600;line-height:22px;display:flex;gap:12px}
.footer .rule{position:absolute;left:0;top:144px;width:100%;height:1px;background:rgba(255,255,255,.18)}
.footer .col{position:absolute;top:176px;font-size:13px;line-height:24px}
.footer .col h3{font-size:17px;font-weight:700;margin-bottom:6px}
.footer .signup{position:absolute;left:811px;top:228px;width:277px;height:36px;display:flex}
.footer .signup span{flex:1;background:var(--white);color:#9aa3aa;font-size:12px;padding:10px 8px}
.footer .signup b{width:38px;background:var(--teal);display:flex;align-items:center;justify-content:center}
.footer .legal{position:absolute;left:811px;top:278px;font-size:10px;line-height:20px;color:#d8e2e9}
.footer .socials{position:absolute;left:112px;top:328px;display:flex;gap:12px}
.footer .bottom{position:absolute;left:0;bottom:0;width:100%;height:43px;background:var(--navy-deep);font-size:13px;display:flex;align-items:center;justify-content:center;color:#dfe7ec}
</style>
</head>
<body>

<div class="block topbar">
  <span class="item"><svg width="12" height="12" viewBox="0 0 24 24"><path fill="#fff" d="M6.6 10.8c1.4 2.8 3.8 5.1 6.6 6.6l2.2-2.2c.3-.3.7-.4 1-.2 1.1.4 2.3.6 3.6.6.6 0 1 .4 1 1V20c0 .6-.4 1-1 1C10.6 21 3 13.4 3 4c0-.6.4-1 1-1h3.5c.6 0 1 .4 1 1 0 1.3.2 2.5.6 3.6.1.3 0 .7-.2 1z"/></svg>08 9000 4172</span>
  <span class="item"><svg width="13" height="10" viewBox="0 0 13 10"><rect width="13" height="10" fill="#fff"/><path d="M0 0l6.5 5L13 0" stroke="#1192b3" fill="none"/></svg>hello@brindlequay.com.au</span>
  <span class="social"><span class="dot" aria-label="social link"></span><span class="dot" aria-label="social link"></span></span>
</div>

<div class="block header">
  <div class="brand">Brindle Quay<small>Proactive Business Accountants</small></div>
  <nav class="nav">
    <svg width="16" height="14" viewBox="0 0 16 14"><path fill="#3d4a55" d="M8 0l8 7h-2v7h-4V9H6v5H2V7H0z"/></svg>
    <span>About</span><span class="active">Services</span><span>Testimonials</span><span>Articles</span><span>Events</span><span>Contact</span>
    <span class="btn">Book A Free Consultation</span>
  </nav>
</div>

<div class="block hero" role="img" aria-label="Photo of the firm's office building at dusk">
  <div class="band"></div>
  <h1>Services</h1>
</div>

<p class="block intro">Tax accounting is what most public practice accountants do. Management Accounting is very different – it's the accounting and reporting done in an organisation to help the owners/leaders make decisions. Both are done by accountants, but a different mind-set and skill-set is required for each. At Brindle Quay, we do both. We regularly see how timely decisions are made using Management Reports that would not have been made – and the positive differences those decisions make to businesses. Larger businesses generate Management Reports regularly (usually monthly) and can't imagine doing business without them. Smaller businesses often haven't discovered them yet and we've seen dramatic turn-arounds in business performance when they have. Hear what an engineering client, Dean, says about management reporting</p>

<section class="block video">
  <svg class="photo" width="620" height="475" viewBox="0 0 620 475" role="img" aria-label="Video still of a client and adviser walking through a warehouse">
    <defs><linearGradient id="wh" x1="0" y1="0" x2="1" y2="1"><stop offset="0" stop-color="#7d8a8c"/><stop offset=".5" stop-color="#a89a80"/><stop offset="1" stop-color="#4d5356"/></linearGradient></defs>
    <polygon points="0,0 615,0 551,475 0,475" fill="url(#wh)"/>
    <circle cx="277" cy="237" r="54" fill="rgba(255,255,255,.35)"/>
    <circle cx="277" cy="237" r="42" fill="#fff"/>
    <polygon points="268,222 268,252 292,237" fill="var(--teal)"/>
  </svg>
  <div class="copy">
    <h2>hospitality client says about<br>management accounting</h2>
    <blockquote>"We have worked with Brindle Quay for over 10 years now and really value the way they keep us focused on the numbers. They have shown us the KPI's we should be tracking in our most recent business venture, which gives us insights into areas that are going well and those that need work. We check in monthly to see how the business is performing against the forecast that we set together and it is great to have someone to be able to bounce ideas off."</blockquote>
  </div>
</section>

<section class="block feature" style="top:1208px">
  <div class="text" style="left:112px;top:18px">
    <h2>What's wrong with no<br>Management Accounting?</h2>
    <p>Every SMB engages an accountant to do their tax accounting (it's the law). Once per year, their nominated tax accountant takes the data from the accounting system (typically Ledgerly or Tallybook) and prepares a report for the ATO (Australian Tax Office) so that the ATO can tell the business how much tax it should pay. The problem is, this reporting is done often 6 months after the end of a financial year, so the information is up to 18 months old. A lot can happen in one month let alone 18 - so this report is far too old to take quick action if things are not going well. [insert image of old accounts]</p>
  </div>
  <div class="img" style="left:625px;top:0;background:linear-gradient(135deg,#d9dde0,#8f9aa3 55%,#e6e8ea)" role="img" aria-label="Photo of a desk with printed accounts, a calculator and a monitor showing spreadsheets"></div>
</section>

<section class="block feature" style="top:1648px">
  <div class="img" style="left:110px;top:0;background:linear-gradient(135deg,#e8e4dc,#a59a88 50%,#5c5448)" role="img" aria-label="Photo of a stone bank building facade"></div>
  <div class="text" style="left:628px;top:-6px">
    <h2>Watching the bank account?</h2>
    <p style="margin-top:8px">Now while the bank account should be watched (not obsessively), too many business owners ONLY monitor their bank account. So what's wrong with this? The problem with the money in your bank account is that much of it might not be yours - either now or in the near future. Similarly, much of your money might currently be in other people's bank accounts. If you always paid cash for your supplies, and always received cash from your customers, then your bank account might be a better reflection of what is happening right now. But, the moment you send or receive an invoice, you're in the debt business. You are lending to, or borrowing money from, the businesses you exchange invoices with. So you need to know how much you owe, and how much you are owed. These debts could be getting out of control and the bank transactions simply aren't going to tell you.</p>
  </div>
</section>

<section class="block plband">
  <h2>The Problem with the Profit &amp; Loss Report</h2>
  <p>The P&amp;L shows you what you earned in the month (or the quarter, or year etc). This is why it is a better indication of your profitability than just the bank transactions (but you still need to read your balance sheet and cash summary - but that's another topic). So why not just print off the P&amp;L and other reports directly from your accounting system? Assuming your bookkeeper has been entering data into you accounting system regularly (and most SMBs are doing this), why don't we just print off a set of reports (P&amp;L, Balance, Cash etc)? Now you could certainly do this, but you will likely find that it will report a very high profit on the P&amp;L (sounds great, but unfortunately it's a fantasy). Apart from allocation errors, there are lots of causes for overstating profit. The common reasons</p>
</section>

<section class="block feature" style="top:2526px">
  <div class="text" style="left:112px;top:36px">
    <h2>Committed future expenses</h2>
    <p>That's not the only problem. When you take on other commitments to fork out cash in future such as employing staff, buying vehicles or plant, or signing a lease, you're committing to that expense (and hoping you'll be able to cover it when the time comes).</p>
    <p style="margin-top:24px">So you see, the bank account is a very late (and inaccurate) indication of what will happen. Businesses are like ships with large turning circles - even a small business can take many months to turn around if things change quickly. You need as much warning as possible of trouble ahead.</p>
  </div>
  <div class="img" style="left:625px;top:0;background:linear-gradient(180deg,#c9d3e6 0%,#7a9cc8 22%,#1f5a96 45%,#0d3f78 100%)" role="img" aria-label="Aerial photo of a cruise ship crossing open ocean"></div>
</section>

<section class="block feature" style="top:2966px">
  <div class="img" style="left:110px;top:0;background:radial-gradient(circle at 55% 45%,#5a4a48 0%,#2a2c3c 45%,#14161f 100%)" role="img" aria-label="Photo of a hand with a stylus over a tablet showing a rising bar chart"></div>
  <div class="text" style="left:628px;top:50px">
    <h2>"Profit" isn't what you might<br>think it is</h2>
    <p style="margin-top:18px">Even when the P&amp;L profit is calculated correctly, the profit it shows is accounting profit and may not align with many business owner's idea or expectations of profit. We need to understand what it means. Buying stock, assets/plant and paying down debt (such as HP loans) will all drain cash but not create a blip on the P&amp;L profit. Plant which you bought years ago but is no longer supporting the business still being depreciated might be correct accounting, but giving you a mis-leading profit figure.</p>
  </div>
</section>

<section class="block cta">
  <p>Please contact us for more information and find out how<br>we can help you feel good about your future.</p>
  <span class="btn-light">Book A Free Consultation</span>
</section>

<footer class="block footer">
  <div class="brand">Brindle Quay<small>Proactive Business Accountants</small></div>
  <div class="contact" style="left:460px">
    <svg width="18" height="26" viewBox="0 0 18 26"><path fill="#fff" d="M9 0a9 9 0 0 0-9 9c0 7 9 17 9 17s9-10 9-17a9 9 0 0 0-9-9zm0 12.5A3.5 3.5 0 1 1 9 5.5a3.5 3.5 0 0 1 0 7z"/></svg>
    <span>Level 2, Harbourview Business Centre<br>18 Merrow Street, Subiaco WA 6008</span>
  </div>
  <div class="contact" style="left:811px">
    <svg width="12" height="44" viewBox="0 0 12 44"><path fill="#fff" d="M2.5 4.5c.8 1.6 2.2 3 3.8 3.8l1.3-1.3c.2-.2.4-.2.6-.1.6.2 1.3.3 2 .3.3 0 .6.3.6.6v2c0 .3-.3.6-.6.6C4.8 10.4.6 6.2.6 1.2.6.9.9.6 1.2.6h2c.3 0 .6.3.6.6 0 .7.1 1.4.3 2 .1.2 0 .4-.1.6z"/><rect x="0" y="27" width="12" height="9" fill="#fff"/><path d="M0 27l6 4.5 6-4.5" stroke="#3e5a70" fill="none"/></svg>
    <span>08 9000 4172<br>hello@brindlequay.com.au</span>
  </div>
  <div class="rule"></div>
  <div class="col" style="left:112px"><h3>Home</h3>About<br>People<br>Our Mission<br>Contact Us</div>
  <div class="col" style="left:374px"><h3>Services</h3>Management Accounting<br>Tax Planning<br>Tax Compliance<br>Bookkeeping<br>Self Managed Super Funds<br>Business Education &amp; Seminars</div>
  <div class="col" style="left:636px"><h3>Link</h3>Testimonials<br>Events<br>Articles</div>
  <div class="col" style="left:811px"><h3>Newsletter Sign up</h3>Receive our free regular knowledge bulletins</div>
  <div class="signup"><span>you@youremail.com.au</span><b><svg width="16" height="14" viewBox="0 0 16 14"><path fill="#fff" d="M0 6l16-6-4 14-4-5z"/></svg></b></div>
  <div class="legal">© 2021, Brindle Quay. All Rights Reserved.<br>Website Design &amp; Hosting by Fieldline Studio</div>
  <div class="socials"><span class="dot" aria-label="social link"></span><span class="dot" aria-label="social link"></span></div>
  <div class="bottom">© 2021 brindlequay. All Rights Reserved.</div>
</footer>

</body>
</html>
```